Need Business Card for our Real Estate Business with Sales Executive's Picture

PANTONE 484 C ( RED)

PANTONE 2766 C ( BLUE

Industry/Entity Type

Real Estate

Contact Information for Business Card

Name, Mobile, email, & picture of Person
Agency Phone, address, Web address

Requirements
Must have
• Our Logo Colours, Agent Picture,

```html
<!DOCTYPE html>
<html lang="en">
<head>
<meta charset="utf-8">
<title>Meridian Real Estate – Business Card</title>
<link rel="stylesheet" href="https://fonts.googleapis.com/css2?family=Archivo:wght@700&family=Work+Sans:wght@400;500&display=swap">
<style>
  :root {
    --navy: #141b4d;
    --red: #8a2a24;
    --white: #ffffff;
    --ink: #2a2d3a;
    --muted: #555a6b;
    --backdrop: #d9d7d3;
    --photo-a: #e8e4e0;
    --photo-b: #3a4a8a;
  }
  * { box-sizing: border-box; margin: 0; padding: 0; }
  html, body { width: 1200px; height: 930px; overflow: hidden; }
  body { background: var(--backdrop); position: relative; font-family: "Work Sans", sans-serif; }

  .card {
    position: absolute;
    width: 560px; height: 320px;
    border-radius: 16px;
    overflow: hidden;
    box-shadow: 0 10px 24px rgba(0,0,0,.25);
  }

  /* Back side */
  .card-back { left: 80px; top: 100px; background: var(--navy); color: var(--white); }
  .card-back .brand {
    position: absolute; left: 0; right: 0; top: 110px;
    display: flex; flex-direction: column; align-items: center; gap: 8px;
  }
  .brand-name {
    font-family: "Work Sans", sans-serif; font-weight: 500;
    font-size: 40px; line-height: 1.1; letter-spacing: 6px; text-transform: uppercase;
    display: flex; align-items: center; gap: 12px;
  }
  .brand-mark { width: 12px; height: 12px; background: currentColor; }
  .brand-rule { width: 300px; height: 1px; background: currentColor; opacity: .8; }
  .brand-sub { font-size: 12px; letter-spacing: 4px; text-transform: uppercase; font-weight: 500; }
  .card-back .address {
    position: absolute; left: 0; right: 0; bottom: 46px;
    text-align: center; font-size: 14px; letter-spacing: .3px;
  }

  /* Front side */
  .card-front { left: 560px; top: 440px; background: var(--white); }
  .agent-photo {
    position: absolute; left: 80px; top: 70px; width: 205px; height: 250px;
    background: linear-gradient(180deg, var(--photo-a) 0%, var(--photo-a) 35%, var(--photo-b) 70%);
    border-radius: 100px 100px 0 0;
  }
  .footer-waves { position: absolute; left: 0; bottom: 0; width: 560px; height: 140px; }
  .card-front .brand {
    position: absolute; right: 34px; top: 22px; color: var(--navy);
    display: flex; flex-direction: column; align-items: center; gap: 5px;
  }
  .card-front .brand-name { font-size: 28px; letter-spacing: 4px; gap: 10px; }
  .card-front .brand-mark { width: 9px; height: 9px; background: var(--red); }
  .card-front .brand-rule { width: 210px; }
  .card-front .brand-sub { font-size: 9px; letter-spacing: 3px; }

  .contact { position: absolute; right: 34px; top: 94px; text-align: right; }
  .agent-name { font-family: "Archivo", sans-serif; font-weight: 700; font-size: 22px; line-height: 1.15; color: var(--navy); letter-spacing: .5px; }
  .agent-role { font-size: 13px; line-height: 1.25; color: var(--muted); margin-bottom: 8px; }
  .contact-list { list-style: none; font-size: 12.5px; color: var(--ink); line-height: 1.5; }
  .contact-list li { display: flex; justify-content: flex-end; align-items: center; gap: 8px; }
  .contact-icon { width: 11px; height: 11px; fill: var(--navy); flex: none; }
</style>
</head>
<body>

<section class="card card-back">
  <div class="brand">
    <div class="brand-name"><span class="brand-mark"></span>Meridian</div>
    <div class="brand-rule"></div>
    <div class="brand-sub">Real Estate</div>
  </div>
  <p class="address">Via dei Tigli, 48. 12030 Revello (CN)</p>
</section>

<section class="card card-front">
  <div class="agent-photo" role="img" aria-label="Portrait photo of the sales executive in a navy suit"></div>
  <svg class="footer-waves" viewBox="0 0 560 140" preserveAspectRatio="none">
    <path d="M0 140 L0 132 C200 122 390 100 560 72 L560 140 Z" fill="var(--navy)"/>
    <path d="M0 127 C200 117 390 95 560 67" fill="none" stroke="var(--white)" stroke-width="4"/>
    <path d="M0 122 C200 112 390 89 560 61" fill="none" stroke="var(--red)" stroke-width="3.5"/>
  </svg>

  <div class="brand">
    <div class="brand-name"><span class="brand-mark"></span>Meridian</div>
    <div class="brand-rule"></div>
    <div class="brand-sub">Real Estate</div>
  </div>

  <div class="contact">
    <div class="agent-name">DANIEL REYES</div>
    <div class="agent-role">Managing Director</div>
    <ul class="contact-list">
      <li>+852 2900 1456 <svg class="contact-icon" viewBox="0 0 24 24"><path d="M6.6 10.8a15 15 0 0 0 6.6 6.6l2.2-2.2a1 1 0 0 1 1-.25 11.4 11.4 0 0 0 3.6.57 1 1 0 0 1 1 1V20a1 1 0 0 1-1 1A17 17 0 0 1 3 4a1 1 0 0 1 1-1h3.5a1 1 0 0 1 1 1c0 1.25.2 2.45.57 3.57a1 1 0 0 1-.25 1z"/></svg></li>
      <li>+852 2900 1478 <svg class="contact-icon" viewBox="0 0 24 24"><rect x="3" y="3" width="18" height="18" rx="3"/></svg></li>
      <li>info@meridianrealestate.com <svg class="contact-icon" viewBox="0 0 24 24"><path d="M2 5h20v14H2z M4 7v.5l8 5 8-5V7z" fill-rule="evenodd"/></svg></li>
      <li>www.meridianrealestate.com <svg class="contact-icon" viewBox="0 0 24 24"><circle cx="12" cy="12" r="10"/></svg></li>
    </ul>
  </div>
</section>

</body>
</html>
```